Business Card - Tidal Lanes

Need Business Card design for company named Tidal Lanes. Software development focused mainly on Brindle Orvix & Zelt Apps. I've attached our logo with both a black and white background. Please add trademark symbol to logo when using.

```html
<!DOCTYPE html>
<html lang="en">
<head>
<meta charset="utf-8">
<title>Tidal Lanes – Business Card</title>
<link href="https://fonts.googleapis.com/css2?family=Source+Sans+3:wght@400;600;700&display=swap" rel="stylesheet">
<style>
  :root {
    --page: #ecebe8;
    --ink: #111111;
    --band: #050505;
    --white: #ffffff;
    --amber-light: #f8c41c;
    --amber-deep: #f29a30;
    --shadow: rgba(0, 0, 0, 0.18);
  }
  * { box-sizing: border-box; margin: 0; padding: 0; }
  html, body {
    width: 1200px;
    height: 720px;
    overflow: hidden;
    background: var(--page);
    font-family: "Source Sans 3", "Helvetica Neue", Arial, sans-serif;
  }
  .canvas {
    position: relative;
    width: 1200px;
    height: 720px;
    display: flex;
    align-items: center;
    justify-content: center;
    gap: 40px;
  }
  .card {
    position: relative;
    width: 520px;
    height: 297px;
    overflow: hidden;
    border-radius: 3px;
    box-shadow: 0 6px 18px var(--shadow);
    background: linear-gradient(100deg, var(--amber-light) 0%, var(--amber-deep) 100%);
  }

  /* Front */
  .card-front .top-band {
    position: absolute;
    left: 0; top: 0;
    width: 100%;
    height: 150px;
    background: var(--band);
  }
  .card-front .brand {
    position: absolute;
    left: 0; right: 0;
    top: 94px;
    text-align: center;
    padding-left: 20px;
    color: var(--white);
    font-weight: 700;
    font-size: 26px;
    letter-spacing: -0.3px;
  }
  .card-front .brand-faint {
    position: absolute;
    right: 36px;
    top: 156px;
    color: var(--white);
    opacity: 0.22;
    font-weight: 700;
    font-size: 24px;
  }
  .contact {
    position: absolute;
    left: 22px;
    top: 190px;
    color: var(--ink);
  }
  .contact .person {
    font-size: 17px;
    margin-bottom: 6px;
  }
  .contact .person-name { font-weight: 700; }
  .contact .person-title { font-weight: 400; font-size: 15px; }
  .contact .line {
    display: flex;
    align-items: center;
    gap: 8px;
    font-size: 14px;
    line-height: 20px;
  }
  .contact .line svg { width: 13px; height: 13px; fill: var(--ink); }
  .contact .address {
    font-size: 11.5px;
    margin-top: 4px;
    padding-left: 21px;
  }

  /* Back */
  .card-back .brand {
    position: absolute;
    inset: 0;
    display: flex;
    align-items: center;
    justify-content: center;
    color: var(--white);
    font-weight: 700;
    font-size: 52px;
    letter-spacing: -0.5px;
  }
</style>
</head>
<body>
  <main class="canvas">
    <section class="card card-front" aria-label="Card front">
      <div class="top-band"></div>
      <div class="brand">Tidal Lanes</div>
      <div class="brand-faint" aria-hidden="true">Tidal Lanes</div>
      <div class="contact">
        <p class="person"><span class="person-name">Your Name,</span> <span class="person-title">Title</span></p>
        <p class="line">
          <svg viewBox="0 0 16 16" aria-hidden="true"><path d="M4 0h8a1 1 0 0 1 1 1v14a1 1 0 0 1-1 1H4a1 1 0 0 1-1-1V1a1 1 0 0 1 1-1zm1 2v9h6V2zm3 10.5a1 1 0 1 0 0 2 1 1 0 0 0 0-2z"/></svg>
          555-204-7710
        </p>
        <p class="line">
          <svg viewBox="0 0 16 16" aria-hidden="true"><path d="M2 6c0-2 2.5-3 6-3s6 1 6 3v1h-3V5.5H5V7H2zm1 2h10l1 6H2zm3 1.5v1.5h1.5V9.5zm2.5 0v1.5H10V9.5zM6 12v1.5h1.5V12zm2.5 0v1.5H10V12z"/></svg>
          555-318-4062
        </p>
        <p class="address">4120 Harbor Row, Bayfield, FL 30412</p>
      </div>
    </section>

    <section class="card card-back" aria-label="Card back">
      <div class="brand">Tidal Lanes</div>
    </section>
  </main>
</body>
</html>
```